Blow Dry Bar Business Cards

These cards must be eye catching and modern.
You must be willing to work fast and make changes.

Winner will be offered other projects

Files 1 THIS IS THE STYLE CARDS I AM INTRESTED IN!!!
Please be creative, I am paying for my own eye catching design. I need files to be nexa press ready.

COLORS THAT ARE PAINTED INSIDE MY SHOP:
- - - http://www.quorvelpaint.example/en/explore-colors/painter/color-selector.html?colors=4007-3C

- - - http://www.brandivex.example/color/paint-colors/hidden-corridor-d58-2

I want the business cards sleek and modern if you use the logo please correct imperfections. I added the part that says Blow Dry Bar (see website).
Do not be afraid to separate the blow dryer from the name to make the cards look like the file with the pink elephant.

SHOULD INCLUDE
*Blow Dryer (we are a blow dry bar not a salon we do not cut or color so do not include sheers of any kind)
*BUSINESS NAME: Simply Swept Upward - Blow Dry Bar (PLEASE SEE MY WEBSITE)
* Website: SIMPLYSWEPTUPWARD.EXAMPLE
*Phone number (555) 014-2763
Updates

Nexa press said it can be submitted in JPG

http://www.brandivex.example/color/paint-colors/hidden-corridor-d58-2 http://www.quorvelpaint.example/en/explore-colors/painter/color-selector.html?colors=4007-3C ^^^^ These links will take you to the color paint that is painted inside my shop.

Target Market(s)

AGES 18 - 55 WOMEN
HIGH END MARKET

Industry/Entity Type

Salon

Requirements
Must have
• SEE COLOR EXAMPLE FILE
BLOW DRYER
UNIQUE
I LIKE THE CARD WITH THE PINK ELEPHANT THE BEST
Nice to have
• BE AS CREATIVE AND MODERN AS POSSIBLE DO NOT COPY ANY OF THE CARDS BELOW.
Should not have
• SCISSORS
PINK

```html
<!DOCTYPE html>
<html lang="en">
<head>
<meta charset="utf-8">
<title>Simply Swept Upward – Business Cards</title>
<link rel="stylesheet" href="https://fonts.googleapis.com/css2?family=Roboto+Condensed:wght@300;400&display=swap">
<style>
  :root{
    --bg:#ece8e3;
    --brown:#461a0f;
    --gold:#f6b914;
    --white:#ffffff;
    --hair-dark:#8a4a22;
    --hair-mid:#c98a4a;
    --hair-light:#ead3ad;
  }
  *{box-sizing:border-box;margin:0;padding:0}
  html,body{width:1200px;height:848px;overflow:hidden;background:var(--bg)}
  body{font-family:"Roboto Condensed",Arial,sans-serif;display:flex;flex-direction:column;align-items:center;justify-content:center;gap:40px}
  .card{width:630px;height:360px;position:relative;overflow:hidden;box-shadow:0 6px 18px rgba(0,0,0,.18)}
  .card-front{background:var(--brown)}
  .card-front .photo{position:absolute;inset:0}
  .brand-block{position:absolute;right:40px;top:40px;text-align:right;color:var(--gold)}
  .brand-name{font-weight:400;font-size:34px;letter-spacing:.5px}
  .tagline{font-weight:300;font-size:30px;margin-top:18px}
  .contact{position:absolute;right:40px;bottom:48px;list-style:none;text-align:right;color:var(--gold);font-weight:300;font-size:15px;line-height:21px;letter-spacing:.3px}
  .contact li{display:flex;justify-content:flex-end;align-items:flex-start;gap:10px}
  .contact svg{width:13px;height:13px;margin-top:4px;flex:none}
  .card-back{background:var(--white);display:flex;align-items:center;justify-content:center;gap:18px}
  .back-name{color:var(--brown);font-weight:400;font-size:54px;letter-spacing:1px}
  .back-dot{width:22px;height:22px;border-radius:50%;background:var(--brown)}
</style>
</head>
<body>
  <section class="card card-front">
    <svg class="photo" viewBox="0 0 630 360" width="630" height="360" role="img" aria-label="Photo of long wavy auburn and blonde blow-dried hair">
      <defs>
        <linearGradient id="hairTone" x1="0" y1="0" x2="1" y2="1">
          <stop offset="0" stop-color="var(--hair-light)"/>
          <stop offset=".45" stop-color="var(--hair-mid)"/>
          <stop offset="1" stop-color="var(--hair-dark)"/>
        </linearGradient>
      </defs>
      <path d="M0 0 H215 C300 90 320 240 265 360 H0 Z" fill="var(--gold)"/>
      <path d="M0 0 H200 C285 90 303 240 250 360 H0 Z" fill="url(#hairTone)"/>
    </svg>
    <div class="brand-block">
      <div class="brand-name">Simply Swept Upward</div>
      <div class="tagline">Blow Dry Bar</div>
    </div>
    <ul class="contact">
      <li>(555) 014-2763
        <svg viewBox="0 0 24 24"><path fill="var(--gold)" d="M6.6 10.8a15 15 0 0 0 6.6 6.6l2.2-2.2a1 1 0 0 1 1-.25 11.4 11.4 0 0 0 3.6.6 1 1 0 0 1 1 1V20a1 1 0 0 1-1 1A17 17 0 0 1 3 4a1 1 0 0 1 1-1h3.5a1 1 0 0 1 1 1c0 1.25.2 2.45.6 3.6a1 1 0 0 1-.25 1z"/></svg></li>
      <li>SIMPLYSWEPTUPWARD.EXAMPLE
        <svg viewBox="0 0 24 24"><circle cx="12" cy="12" r="10" fill="none" stroke="var(--gold)" stroke-width="2"/><path d="M2 12h20M12 2c3 3 3 17 0 20M12 2c-3 3-3 17 0 20" fill="none" stroke="var(--gold)" stroke-width="1.6"/></svg></li>
      <li>INFO@SIMPLYSWEPTUPWARD.EXAMPLE
        <svg viewBox="0 0 24 24"><rect x="2" y="5" width="20" height="14" fill="var(--gold)"/><path d="M2 5l10 8 10-8" fill="none" stroke="var(--brown)" stroke-width="1.6"/></svg></li>
      <li>27 HARBOR FERN LANE SUITE 4<br>MILLBROOK COVE, TEXAS 75010
        <svg viewBox="0 0 24 24"><path fill="none" stroke="var(--gold)" stroke-width="2" d="M12 22s-7-7.5-7-13a7 7 0 0 1 14 0c0 5.5-7 13-7 13z"/><circle cx="12" cy="9" r="2.5" fill="var(--gold)"/></svg></li>
    </ul>
  </section>

  <section class="card card-back">
    <div class="back-name">Simply Swept Upward</div>
    <div class="back-dot" aria-hidden="true"></div>
  </section>
</body>
</html>
```